Business Cards for IT Consulting Company (Managed Service Provider)

I am looking to have some business cards printed and would like some designs. We are an IT Consulting company based in Vancouver BC. I would like a nice clean and modern look to the cards. I have uploaded all the versions of my logo so parts can be used as needed. Here is a snippit from our website homepage:

Quillbrook Networks Ltd. is an IT Solutions Partner located in Vancouver BC, Canada. We offer IT solutions and support to customers in the greater Vancouver Area. With expertise in Microsoft platforms, as well as Linux and Mac OSX and over 12 years experience in the IT industry, Quillbrook Networks is dedicated to offering our clients top quality service and products. We take pride in the solutions we offer our customers. The greatest compliment a client can give us is to recommend our services.

Quillbrook Networks Ltd. offers a wide range of IT services from onsite service to remote support and managed service solutions. This allows clients to choose the support path that best suits their company’s needs. Supporting many different sized companies from small to enterprise level over the past 12 years Quillbrook Networks has the experience and expertise needed to ensure things run smoothly. Allowing our clients to focus on doing business.

Revolutionizing the way IT services are delivered.

Quillbrook Networks is dedicated to providing our clients with IT solutions that work and grow with them for years to come. This philosophy helps save money in the long run instead of replacing equipment constantly. Far too often IT solutions are not well thought out and while possibly solving the problem at hand, require replacement due to growth or quality within a very short time frame. Quillbrook Networks takes pride in providing solutions that will last and be able to accommodate growth without the need for replacement.

Industry/Entity Type

Information Technology

Contact Information for Business Card

Quillbrook Networks Ltd.
(Employee Name)
Eml: (Employees Email Address)
Web: quillbrook.me
Ph: 604-555-0148

Font styles to use
Serif
Sans Serif

Requirements
Must have
• The Company logo and company colors.
Nice to have
• - Our tag line: "Dependable IT Done Right" or "Revolutionizing the way IT services are delivered."
• - Also I really like the idea of nature and technology together blending which is sort of where my logo came from so integrating that somehow onto the business cards would be great.

```html
<!DOCTYPE html>
<html lang="en">
<head>
<meta charset="utf-8">
<title>Quillbrook Networks Ltd. — Business Card</title>
<link href="https://fonts.googleapis.com/css2?family=Montserrat:wght@500;600;700&display=swap" rel="stylesheet">
<style>
  :root {
    --backdrop: #2b2b2d;
    --card-black: #000000;
    --card-white: #ffffff;
    --brand-blue: #1aa3e8;
    --text-grey: #4a4a4a;
    --text-white: #ffffff;
  }
  * { margin: 0; padding: 0; box-sizing: border-box; }
  html, body {
    width: 1200px; height: 900px; overflow: hidden;
    background: var(--backdrop);
    font-family: "Montserrat", sans-serif;
  }
  .stage { position: relative; width: 1200px; height: 900px; }

  .card {
    position: absolute; width: 700px; height: 400px;
    border-radius: 26px; overflow: hidden;
    box-shadow: 0 18px 40px rgba(0,0,0,0.45);
  }

  /* Back side */
  .card-back { left: 100px; top: 50px; background: var(--card-black); }
  .back-brand {
    position: absolute; left: 0; right: 0; top: 120px;
    display: flex; align-items: center; justify-content: center; gap: 16px;
    color: var(--brand-blue); font-weight: 600; font-size: 40px; letter-spacing: 0.5px;
  }
  .back-brand .brand-square {
    width: 34px; height: 34px; border: 4px solid var(--brand-blue);
  }
  .back-tagline-rule {
    position: absolute; left: 0; right: 0; top: 330px; height: 5px;
    background: var(--brand-blue);
  }
  .back-tagline {
    position: absolute; left: 0; right: 0; top: 340px;
    text-align: center; color: var(--text-white);
    font-weight: 600; font-size: 19px; letter-spacing: 0.6px;
  }
  .back-edge-bar {
    position: absolute; left: 0; right: 0; bottom: 0; height: 24px;
    background: var(--brand-blue);
  }

  /* Front side */
  .card-front { left: 420px; top: 470px; background: var(--card-white); }
  .front-curve { position: absolute; inset: 0; }
  .front-brand {
    position: absolute; left: 40px; top: 112px;
    display: flex; align-items: center; gap: 14px;
    color: var(--brand-blue); font-weight: 600; font-size: 34px;
  }
  .front-brand .brand-square {
    width: 30px; height: 30px; border: 4px solid var(--brand-blue);
  }
  .person {
    position: absolute; left: 40px; top: 286px; text-align: right;
  }
  .person-name {
    color: var(--brand-blue); font-weight: 700; font-size: 27px; letter-spacing: 1.5px;
  }
  .person-role {
    color: var(--text-grey); font-weight: 600; font-size: 15px; letter-spacing: 1.5px; margin-top: 2px;
  }
  .divider {
    position: absolute; left: 370px; top: 270px; width: 2px; height: 80px;
    background: var(--brand-blue);
  }
  .contact-list {
    position: absolute; left: 392px; top: 262px; list-style: none;
    color: var(--text-grey); font-weight: 500; font-size: 16px; letter-spacing: 0.5px;
  }
  .contact-list li { display: flex; align-items: center; gap: 10px; height: 28px; }
  .contact-list svg { width: 13px; height: 13px; fill: var(--brand-blue); flex: none; }
</style>
</head>
<body>
<main class="stage">

  <section class="card card-back" aria-label="Card back">
    <div class="back-brand"><span class="brand-square"></span><span>Quillbrook Networks</span></div>
    <div class="back-tagline-rule"></div>
    <p class="back-tagline">Dependable IT Done Right</p>
    <div class="back-edge-bar"></div>
  </section>

  <section class="card card-front" aria-label="Card front">
    <svg class="front-curve" viewBox="0 0 700 400" preserveAspectRatio="none" aria-hidden="true">
      <path d="M0 0 H700 V40 Q420 300 0 232 Z" fill="#000000"/>
      <path d="M0 232 Q420 300 700 40" fill="none" stroke="#1aa3e8" stroke-width="6"/>
    </svg>
    <div class="front-brand"><span class="brand-square"></span><span>Quillbrook Networks Ltd.</span></div>
    <div class="person">
      <p class="person-name">MARLON KEATS</p>
      <p class="person-role">DIRECTOR</p>
    </div>
    <div class="divider"></div>
    <ul class="contact-list">
      <li><svg viewBox="0 0 24 24"><path d="M6.6 10.8a15 15 0 0 0 6.6 6.6l2.2-2.2a1 1 0 0 1 1-.25 11.4 11.4 0 0 0 3.6.57 1 1 0 0 1 1 1V20a1 1 0 0 1-1 1A17 17 0 0 1 3 4a1 1 0 0 1 1-1h3.5a1 1 0 0 1 1 1c0 1.250.2 2.450.57 3.570a1 1 0 0 1-.25 1z"/></svg>604-555-0148</li>
      <li><svg viewBox="0 0 24 24"><path d="M2 5h20v14H2z M4 7v.5l8 5 8-5V7l-8 5z" fill-rule="evenodd"/></svg>info@marlonkeats.com</li>
      <li><svg viewBox="0 0 24 24"><circle cx="12" cy="12" r="10"/></svg>www.quillbrook.me</li>
    </ul>
  </section>

</main>
</body>
</html>
```